UK Online Auction Site needs a clever design

We need a contemporary landing page and registration page design for a UK auction website, that look equally at home on PC's and tablets . The design should be fresh, bright, clean, professional, robust, and familiar. We would like to see something clever but functional.

Online

```html
<!DOCTYPE html>
<html lang="en">
<head>
<meta charset="utf-8">
<title>Bidwell – UK Online Auctions</title>
<link href="https://fonts.googleapis.com/css2?family=Open+Sans:wght@400;600;700&family=Oswald:wght@400;500&display=swap" rel="stylesheet">
<style>
:root{
  --blue:#0a86cf;
  --blue-dark:#0672b3;
  --ink:#333;
  --muted:#666;
  --line:#dcdcdc;
  --panel:#f1f1f1;
  --topbar:#2c2c2c;
  --footer:#3a3b3d;
  --footer-bottom:#333436;
  --red:#e1261c;
  --white:#fff;
}
*{box-sizing:border-box;margin:0;padding:0}
html,body{width:745px;height:1200px;overflow:hidden}
body{position:relative;font-family:"Open Sans",sans-serif;color:var(--ink);background:var(--white);font-size:9px}
.abs{position:absolute}
.topbar{left:0;top:0;width:745px;height:25px;background:var(--topbar)}
.topbar .welcome{left:528px;top:6px;color:#ddd;font-size:9px}
.btn-reg{left:575px;top:5px;width:42px;height:15px;background:#eee;color:#333;font-size:8.5px;text-align:center;line-height:15px;border-radius:1px}
.btn-sign{left:622px;top:5px;width:43px;height:15px;background:var(--blue);color:#fff;font-size:8.5px;text-align:center;line-height:15px;border-radius:1px}
.header{left:0;top:25px;width:745px;height:33px;background:var(--white)}
.brand{left:82px;top:31px;height:20px;display:flex;align-items:center;gap:5px;color:var(--blue);font-weight:700;font-size:15px}
.brand .dot{width:10px;height:10px;border-radius:50%;background:var(--blue)}
.nav{right:81px;top:37px;display:flex;gap:16px;font-size:8.5px;color:#444}
.nav span::after{content:" ▾";font-size:7px}
.band{left:0;top:58px;width:745px;height:36px;background:var(--blue)}
.cat-head{left:82px;top:66px;width:135px;height:20px;background:var(--blue-dark);color:#fff;font-size:10px;line-height:20px;padding-left:7px}
.cat-head svg{position:absolute;right:6px;top:4px}
.cat-list{left:82px;top:86px;width:135px;height:209px;border:1px solid var(--line);border-top:none;background:#fff;list-style:none;padding:0 9px}
.cat-list li{height:22.7px;line-height:22.7px;border-bottom:1px solid #e6e6e6;font-size:8px;color:#555;padding-left:0}
.cat-list li:last-child{border:none}
.select{left:229px;top:67px;width:208px;height:18px;background:#fff;font-size:7px;padding-left:8px;line-height:18px}
.select::after{content:"▼";position:absolute;right:5px;font-size:7px}
.search{left:440px;top:67px;width:177px;height:18px;background:#fff;font-size:6.5px;color:#aaa;line-height:18px;padding-left:14px}
.search svg{position:absolute;left:4px;top:5px}
.search-btn{left:617px;top:67px;width:47px;height:18px;background:var(--blue-dark);border:1px solid #fff;color:#fff;font-size:8.5px;text-align:center;line-height:16px}
.banner{left:229px;top:102px;width:435px;height:193px;border:1px solid var(--line);background:#fcfafa}
.banner h2{position:absolute;left:24px;top:42px;font-family:"Oswald",sans-serif;font-weight:500;color:var(--blue);font-size:23px;letter-spacing:-.3px}
.banner .sub{position:absolute;left:32px;top:81px;font-family:"Oswald",sans-serif;color:#555;font-size:10px}
.banner .deal{position:absolute;left:64px;top:100px;font-family:"Oswald",sans-serif;color:var(--red);display:flex;align-items:flex-end;gap:4px}
.deal .get{font-size:17px;line-height:22px}
.deal .num{font-size:31px;line-height:34px}
.deal .pct{font-size:13px;line-height:13px;display:flex;flex-direction:column;margin-bottom:2px}
.deal .pct em{font-style:normal;color:#777;font-size:13px}
.banner .shop{position:absolute;left:70px;top:146px;width:77px;height:23px;background:var(--blue);color:#fff;font-family:"Oswald",sans-serif;font-size:10px;text-align:center;line-height:23px}
.banner .photo{position:absolute;left:206px;top:6px;width:226px;height:155px;background:linear-gradient(135deg,#fff 30%,#e3e5e8 60%,#2b2d31 100%)}
.features{left:81px;top:310px;width:583px;height:85px;border:4px solid #eee;background:#fff}
.feature{position:absolute;top:24px;width:150px;display:flex;gap:6px}
.feature .ic{width:32px;height:32px;border:2px solid var(--blue);border-radius:50%;flex:none;display:flex;align-items:center;justify-content:center}
.feature b{display:block;font-size:7px;font-weight:600;color:#222;margin-bottom:2px}
.feature p{font-size:6.5px;color:#666;line-height:10px}
.divider{position:absolute;top:15px;width:1px;height:48px;background:var(--line)}
.section-title{font-size:13px;color:#222}
.rule{height:1px;background:var(--line);width:584px;left:81px}
.rule::before{content:"";position:absolute;left:0;top:-1px;width:27px;height:2px;background:var(--blue)}
.arrow{width:16px;height:16px;border-radius:50%;background:#ddd}
.arrow svg{display:block;margin:4px 0 0 5px}
.grid{left:81px;width:583px;height:213px;border:1px solid var(--line);background:var(--panel)}
.card{position:absolute;top:12px;width:131px;height:188px;border:1px solid var(--line);background:#ededed;text-align:center}
.card .img{height:137px;background:#fff;border-bottom:1px solid var(--line);display:flex;align-items:center;justify-content:center}
.card .img div{border-radius:4px}
.card .t{font-size:7.5px;color:#555;margin-top:12px}
.card .p{font-size:7px;color:#777;margin-top:8px}
.card .p b{color:var(--blue);font-weight:400}
.footer{left:0;top:966px;width:745px;height:186px;background:var(--footer);color:#ddd}
.footer h4{position:absolute;top:21px;font-weight:400;font-size:11px;color:#eee}
.footer .col{position:absolute;font-size:7px;line-height:14.5px;color:#ddd}
.links{font-size:8.5px!important}
.field{position:absolute;left:177px;width:130px;height:19px;border:1px solid #999;background:#555;font-size:7px;color:#bbb;line-height:17px;padding-left:6px}
.subscribe{position:absolute;left:177px;top:136px;width:75px;height:21px;background:var(--blue);color:#fff;font-weight:600;font-size:10px;text-align:center;line-height:21px}
.tweet{position:absolute;left:348px;width:150px;font-size:7px;line-height:14.5px}
.tweet::before{content:"";position:absolute;left:0;top:3px;width:13px;height:13px;border-radius:50%;background:#aaa}
.tweet p{padding-left:20px}
.bottom{left:0;top:1152px;width:745px;height:48px;background:var(--footer-bottom);color:#ddd;font-size:8px}
.bottom .copy{position:absolute;left:80px;top:18px}
.social{position:absolute;left:583px;top:15px;display:flex;gap:5px}
.social span{width:16px;height:16px;border-radius:50%;background:#999}
.bottom .code{position:absolute;left:705px;top:17px;font-size:9px}
</style>
</head>
<body>

<div class="abs topbar">
  <span class="abs welcome">Welcome!</span>
</div>
<div class="abs btn-reg">Register</div>
<div class="abs btn-sign">Sign In</div>

<header class="abs header"></header>
<div class="abs brand"><span class="dot"></span>Bidwell</div>
<nav class="abs nav"><span>Sell</span><span>Sign In</span><span>Basket</span><span>Help</span><span>Contact</span></nav>

<div class="abs band"></div>
<div class="abs cat-head">Shop By Categories
  <svg width="12" height="12" viewBox="0 0 12 12"><circle cx="6" cy="6" r="5" fill="none" stroke="#fff"/><path d="M3.5 5l2.5 2.5L8.5 5" fill="none" stroke="#fff"/></svg>
</div>
<ul class="abs cat-list">
  <li>All Categories</li><li>Fashion</li><li>Home &amp; Garden</li><li>Electricals &amp; Technology</li><li>Collectables &amp; Antiques</li><li>Jewellery &amp; Beauty</li><li>Toys</li><li>Sport &amp; Leisure</li><li>Motors</li>
</ul>
<div class="abs select">All Categories</div>
<div class="abs search">
  <svg width="7" height="7" viewBox="0 0 7 7"><circle cx="3" cy="3" r="2.2" fill="none" stroke="#888"/><path d="M4.6 4.6L6.6 6.6" stroke="#888"/></svg>Enter any keyword
</div>
<div class="abs search-btn">Search</div>

<section class="abs banner">
  <div class="photo" role="img" aria-label="Compact camera and tablet product photo"></div>
  <h2>The Smartest Cameras</h2>
  <div class="sub">Even if you’re new or already experienced</div>
  <div class="deal"><span class="get">Get</span><span class="num">50</span><span class="pct">%<em>Off</em></span></div>
  <div class="shop">Shop Now!</div>
</section>

<section class="abs features">
  <div class="feature" style="left:27px">
    <div class="ic"><svg width="16" height="16" viewBox="0 0 16 16"><path d="M8 1l6 2v5c0 4-3 6-6 7-3-1-6-3-6-7V3z" fill="#2e9b3a"/><path d="M5 8l2 2 4-4" fill="none" stroke="#fff" stroke-width="1.6"/></svg></div>
    <div><b>Completely safe</b><p>Bid on or buy items you're watching or searching for</p></div>
  </div>
  <div class="divider" style="left:180px"></div>
  <div class="feature" style="left:231px">
    <div class="ic"><svg width="16" height="16" viewBox="0 0 16 16"><path d="M4 2h8v4a4 4 0 0 1-8 0z" fill="#e0a823"/><rect x="7" y="10" width="2" height="3" fill="#e0a823"/><rect x="5" y="13" width="6" height="2" fill="#c98f12"/></svg></div>
    <div><b>Premium sellers</b><p>Bid on or buy items you're watching or searching for</p></div>
  </div>
  <div class="divider" style="left:393px"></div>
  <div class="feature" style="left:432px">
    <div class="ic"><svg width="20" height="12" viewBox="0 0 20 12"><rect x="1" y="2" width="18" height="8" rx="2" fill="var(--blue)"/><circle cx="5" cy="6" r="1" fill="#fff"/><circle cx="8" cy="6" r="1" fill="#fff"/><circle cx="11" cy="6" r="1" fill="#fff"/><circle cx="14" cy="6" r="1" fill="#fff"/></svg></div>
    <div><b>Feedback rating system</b><p>Bid on or buy items you're watching or searching for</p></div>
  </div>
</section>

<h3 class="abs section-title" style="left:81px;top:413px">Featured</h3>
<div class="abs arrow" style="left:647px;top:415px"><svg width="6" height="8" viewBox="0 0 6 8"><path d="M1 1l3 3-3 3" fill="none" stroke="#fff" stroke-width="1.5"/></svg></div>
<div class="abs rule" style="top:436px"></div>
<section class="abs grid" style="top:450px">
  <div class="card" style="left:12px"><div class="img"><div role="img" aria-label="DSLR camera photo" style="width:82px;height:74px;background:linear-gradient(160deg,#555,#111)"></div></div><p class="t">Test additional shipping per item</p><p class="p"><b>C $10.00</b> 30d, 0h</p></div>
  <div class="card" style="left:155px"><div class="img"><div role="img" aria-label="Antique wall clock photo" style="width:48px;height:76px;background:linear-gradient(#8a4a25,#f4ead8 50%,#6b3518)"></div></div><p class="t">Test additional shipping per item</p><p class="p"><b>C $10.00</b> 30d, 0h</p></div>
  <div class="card" style="left:298px"><div class="img"><div role="img" aria-label="Beauty products on shelf photo" style="width:114px;height:50px;background:linear-gradient(90deg,#e8d6b0,#c9a36a,#f0e2c6,#b97a3a)"></div></div><p class="t">Test additional shipping per item</p><p class="p"><b>C $10.00</b> 30d, 0h</p></div>
  <div class="card" style="left:440px"><div class="img"><div role="img" aria-label="Handbag and vase photo" style="width:66px;height:55px;background:linear-gradient(90deg,#2a3f9a 55%,#b58a3c)"></div></div><p class="t">Test additional shipping per item</p><p class="p"><b>C $10.00</b> 30d, 0h</p></div>
</section>

<h3 class="abs section-title" style="left:80px;top:685px">Items from seller stores</h3>
<div class="abs arrow" style="left:647px;top:688px"><svg width="6" height="8" viewBox="0 0 6 8"><path d="M1 1l3 3-3 3" fill="none" stroke="#fff" stroke-width="1.5"/></svg></div>
<div class="abs rule" style="top:708px"></div>
<section class="abs grid" style="top:722px">
  <div class="card" style="left:12px"><div class="img"><div role="img" aria-label="Silver ring photo" style="width:50px;height:50px;border-radius:50%;background:radial-gradient(circle,#fff 45%,#aaa 50%,#eee 62%,#fff 66%)"></div></div><p class="t">Test additional shipping per item</p><p class="p"><b>C $10.00</b> 30d, 0h</p></div>
  <div class="card" style="left:155px"><div class="img"><div role="img" aria-label="Compact camera and tablet photo" style="width:78px;height:36px;background:linear-gradient(90deg,#222,#555,#333)"></div></div><p class="t">Test additional shipping per item</p><p class="p"><b>C $10.00</b> 30d, 0h</p></div>
  <div class="card" style="left:298px"><div class="img"><div role="img" aria-label="Red cable photo" style="width:62px;height:30px;border-radius:50%;border:3px solid #d8191e"></div></div><p class="t">Test additional shipping per item</p><p class="p"><b>C $10.00</b> 30d, 0h</p></div>
  <div class="card" style="left:440px"><div class="img"><div role="img" aria-label="Tablet with keyboard photo" style="width:62px;height:40px;background:linear-gradient(#444 60%,#eee 60%)"></div></div><p class="t">Test additional shipping per item</p><p class="p"><b>C $10.00</b> 30d, 0h</p></div>
</section>

<footer class="abs footer">
  <h4 style="left:80px">Information</h4>
  <div class="col links" style="left:81px;top:46px">bidwell.co.uk<br>Buy<br>Sell<br>Support<br>Other</div>
  <h4 style="left:177px">Newsletter</h4>
  <div class="col" style="left:177px;top:42px">Sign up with your name and email<br>to get updates fresh updates.</div>
  <div class="field" style="top:77px">Name:</div>
  <div class="field" style="top:107px">Email:</div>
  <div class="subscribe">SUBSCRIBE</div>
  <h4 style="left:348px">Latest Tweets</h4>
  <div class="tweet" style="top:41px"><p>@Lotkeeper Please kindly use our Support Forum:&nbsp; northlot.co.uk.<br>about a month ago</p></div>
  <div class="tweet" style="top:98px"><p>@Lotkeeper Please kindly use our Support Forum:&nbsp; northlot.co.uk.<br>about a month ago</p></div>
  <h4 style="left:523px">Contact Us</h4>
  <div class="col" style="left:524px;top:41px;width:142px">Bidwell Support auctor, nisi elit consequ at ipsum, nec sagittis sem.</div>
  <div class="col" style="left:525px;top:77px">Harbour Ltd, 14 Quay Street,<br>Bristol, UK</div>
  <div class="col" style="left:525px;top:112px">www.bidwell-help.com</div>
  <div class="col" style="left:525px;top:132px">(+44) 117 496 0123</div>
</footer>
<div class="abs bottom">
  <span class="copy">Copyright ©2014, Gavelry Inc.</span>
  <div class="social"><span></span><span></span><span></span><span></span></div>
  <span class="code">C4</span>
</div>

</body>
</html>
```